banner for website

I need a new banner for my website. My website now is. www.brightmeadowkitchen.com, but I'm changing it to Bright Meadow Table and I need a new banner. I want me to be who it's about. I am my brand. I'm Carla Whitford. So, my name needs to be prominent in the banner along with my photo, which I'm attaching. I want my photo very prominent in the banner and very large. I am attaching my two favorites.
I need the banner plain ( with out the newsletter sign up optin part), so I can use it on my newsletters, emails and letter head, as well. I would like it to be inviting. I I have a certain color scheme I use. Deep dark brown letters with blues and greens. Very earthy and psychologically grounded. I would like to keep that color scheme. In my website banner, I need a opt in to sign up for my free monthly newsletter and receive my Free Pantry Basket Planner.

I want the shopping guide to be small and pleasant looking and to say: "Sign up to receive your Free Pantry Basket Planner and monthly newsletter."

I only want my banner to say: "Bright Meadow Table" "Carla Whitford"

I would also like to have part of the banner without the sign in for the newsletter part off of it. And also one with only the "Bright Meadow Table" and one with "Bright Meadow Table" and "Carla Whitford" without the newsletter sign up part on it either.

I hope you can do this for me. I look forward to seeing your design! Sincerely, Carla
Updates

Project Deadline Extended Reason: I couldn't view the designs so I couldn't look at the ones submitted. I just now got into the website with your company's help. I don't want to be penalized because of a problem with the log in at your site. That was not my fault. Please let me know your thoughts. Added Monday, May 9, 2016

Target Market(s)

people over 40 who have bad health or who want to learn how to be a vegetarian for better health.

Number of Pages Required

1 page

Requirements
Must have
• I want the shopping guide to be small and pleasant looking and to say: "Sign up to receive your Free Pantry Basket Planner and monthly newsletter." I would like it to blend and be elegant and not in the middle of the banner or across my face.
• I only want my banner to say: "Bright Meadow Table" "Carla Whitford"
• I would also like to have part of the banner without the sign in for the newsletter part off of it. And also one with only the "Bright Meadow Table" and one with "Bright Meadow Table" and "Carla Whitford" without the newsletter sign up part on it either.
Nice to have
• Nice font and colors. I want the background to be plants and earthy and inviting.
Should not have
• I updated and added two new photos. I think the one you were using with me in the red top looked funny under my eyes. it was too pink or something. I uploaded a better version of that photo. in hopes that it looks better. Please switch those out if you are using the one with me in the red top.

```html
<!DOCTYPE html>
<html lang="en">
<head>
<meta charset="utf-8">
<title>Bright Meadow Table – Website Banner</title>
<link href="https://fonts.googleapis.com/css2?family=Barlow:wght@400&family=Barlow+Semi+Condensed:ital,wght@0,500;1,700&family=Damion&display=swap" rel="stylesheet">
<style>
  :root {
    --canvas: #ffffff;
    --sky: #9fc8ea;
    --ink: #1d3658;
    --mark: #ffffff;
    --caption: #111111;
    --photo-light: #e9c9a8;
    --photo-mid: #c79a6e;
    --photo-dark: #6b5a44;
  }
  * { margin: 0; padding: 0; box-sizing: border-box; }
  html, body {
    width: 1200px; height: 1000px; overflow: hidden;
    background: var(--canvas);
  }
  .stage { position: relative; width: 1200px; height: 1000px; }
  .banner {
    position: absolute; left: 0; top: 399px;
    width: 1200px; height: 202px;
    background: var(--sky);
    overflow: hidden;
  }
  .portrait { position: absolute; left: 0; top: 0; }
  .brand-dot {
    position: absolute; left: 285px; top: 50px;
    width: 96px; height: 96px; border-radius: 50%;
    background: var(--mark);
  }
  .brand-name {
    position: absolute; left: 405px; top: 44px;
    font-family: "Barlow", sans-serif; font-weight: 400;
    font-size: 46px; line-height: 52px;
    color: var(--ink);
  }
  .optin {
    position: absolute; left: 730px; top: 14px; width: 450px;
    text-align: center; color: var(--ink);
  }
  .person-name {
    font-family: "Damion", cursive;
    font-size: 64px; line-height: 90px;
    font-weight: 400;
  }
  .optin-text {
    font-family: "Barlow Semi Condensed", sans-serif;
    font-weight: 500; font-size: 25px; line-height: 29px;
  }
  .optin-text em { font-style: italic; font-weight: 700; }
  .size-note {
    position: absolute; right: 24px; top: 616px;
    font-family: Arial, Helvetica, sans-serif;
    font-size: 16px; color: var(--caption);
  }
</style>
</head>
<body>
<div class="stage">
  <section class="banner">
    <svg class="portrait" width="305" height="202" viewBox="0 0 305 202" role="img" aria-label="Portrait photo of Carla Whitford, smiling, with long blonde hair">
      <defs>
        <linearGradient id="portraitTone" x1="0" y1="0" x2="1" y2="1">
          <stop offset="0" stop-color="var(--photo-mid)"/>
          <stop offset="0.5" stop-color="var(--photo-light)"/>
          <stop offset="1" stop-color="var(--photo-dark)"/>
        </linearGradient>
      </defs>
      <path d="M0 0 H190 C215 40 230 90 240 130 C255 165 285 180 302 202 H0 Z" fill="url(#portraitTone)"/>
    </svg>

    <span class="brand-dot" aria-hidden="true"></span>
    <h1 class="brand-name">Bright Meadow<br>Table</h1>

    <div class="optin">
      <h2 class="person-name">Carla Whitford</h2>
      <p class="optin-text">Sign up for Carla’s free monthly newsletter<br>and receive her <em>Free Pantry Basket Planner.</em></p>
    </div>
  </section>
  <p class="size-note">1408px x 238px</p>
</div>
</body>
</html>
```